Create a step-by-step donors pamphlet for VELTO church

I am looking to get a professionally design pamphlet that gives our donors easy steps to set up reoccurring donation through our give platform.

The ideal design should look professional and creative. No templates or weak AIs.

I've provided church logos and a text file which contains the content of the pamphlet we are trying to make.

Font styles to use
Sans Serif

Requirements
Must have
• Good branding

```html
<!DOCTYPE html>
<html lang="en">
<head>
<meta charset="UTF-8">
<title>VELTO Church – Recurring Donor Pamphlet</title>
<link rel="stylesheet" href="https://fonts.googleapis.com/css2?family=Montserrat:wght@500;600;700;800;900&family=Inter:wght@400;500;600&display=swap">
<style>
  :root {
    --bg: #d9d9db;
    --ink: #121212;
    --black: #0d0d0d;
    --white: #ffffff;
    --orange: #e0641c;
    --orange-deep: #c9470f;
    --amber: #f6a521;
    --flame-red: #a8240c;
    --grey-text: #3a3a3a;
    --rule: #cfcfcf;
  }
  * { box-sizing: border-box; margin: 0; padding: 0; }
  html, body { width: 1200px; height: 900px; overflow: hidden; }
  body {
    background: var(--bg);
    font-family: "Inter", Arial, sans-serif;
    color: var(--ink);
    position: relative;
  }
  .pamphlet {
    position: absolute;
    left: 20px; top: 45px;
    width: 1160px; height: 810px;
    display: flex; gap: 16px;
  }
  .panel {
    position: relative;
    width: 376px; height: 810px;
    overflow: hidden;
  }
  .flame {
    position: absolute;
    background: radial-gradient(ellipse at 50% 85%, var(--amber) 0%, var(--orange) 35%, var(--flame-red) 65%, rgba(13,13,13,0) 100%);
  }

  /* ---------- Cover ---------- */
  .cover { background: var(--black); }
  .cover-top {
    position: absolute; left: 0; top: 0; width: 100%; height: 120px;
  }
  .cover-kicker {
    position: absolute; top: 28px; left: 0; width: 100%;
    text-align: center;
    font-family: "Montserrat", sans-serif; font-weight: 800;
    font-size: 15px; letter-spacing: .3px; color: var(--ink);
  }
  .cover-icon {
    position: absolute; left: 28px; top: 150px;
    width: 46px; height: 58px; border-radius: 50% 50% 45% 45%;
    background: linear-gradient(180deg, var(--amber), var(--orange-deep));
  }
  .cover-title {
    position: absolute; left: 0; top: 250px; width: 100%;
    text-align: center;
    font-family: "Montserrat", sans-serif; font-weight: 800;
    font-size: 48px; line-height: 1.08; color: var(--white);
    text-transform: uppercase;
  }
  .cover-title .accent { display: block; padding-left: 110px; color: var(--amber); }
  .cover-lead {
    position: absolute; left: 50px; right: 50px; top: 535px;
    text-align: center; font-size: 11px; line-height: 1.6; color: #d8d8d8;
  }
  .brand {
    font-family: "Montserrat", sans-serif; font-weight: 700;
    letter-spacing: .5px;
  }
  .cover-brand {
    position: absolute; left: 0; width: 100%; top: 615px; text-align: center;
  }
  .cover-brand .brand-name { font-size: 34px; color: var(--white); }
  .brand-tag {
    font-family: "Montserrat", sans-serif; font-weight: 700;
    font-size: 8px; letter-spacing: 1.5px; color: var(--orange);
    margin-top: 2px;
  }
  .cover-foot {
    position: absolute; bottom: 28px; width: 100%; text-align: center;
    font-family: "Montserrat", sans-serif; font-weight: 700;
    font-size: 10px; letter-spacing: 1px; color: var(--white);
  }

  /* ---------- Inside (middle) ---------- */
  .inside { background: var(--bg); display: flex; flex-direction: column; gap: 20px; }
  .inside-card {
    position: relative; background: var(--white); overflow: hidden;
  }
  .invite { height: 280px; }
  .steps-overview { height: 510px; }
  .card-content { position: relative; padding: 24px 44px 0; text-align: center; }
  .pill {
    display: inline-block;
    background: var(--orange); color: var(--white);
    font-family: "Montserrat", sans-serif; font-weight: 700;
    font-size: 14px; letter-spacing: 1px; text-transform: uppercase;
    padding: 6px 28px; border-radius: 18px;
  }
  .invite-title {
    margin-top: 22px;
    font-family: "Montserrat", sans-serif; font-weight: 700;
    font-size: 21px; line-height: 1.3; color: var(--orange-deep);
  }
  .body-copy { font-size: 9.5px; line-height: 1.55; color: var(--grey-text); margin-top: 16px; }
  .benefits { display: flex; justify-content: space-between; margin-top: 16px; }
  .benefit { width: 80px; text-align: center; font-size: 8.5px; line-height: 1.4; color: var(--grey-text); }
  .benefit-icon {
    width: 46px; height: 46px; border-radius: 50%;
    border: 2px solid var(--orange); margin: 0 auto 8px;
    display: flex; align-items: center; justify-content: center;
  }
  .step-columns { display: flex; margin-top: 22px; }
  .step-col {
    flex: 1; text-align: center; padding: 0 8px;
    font-size: 9px; line-height: 1.45; color: var(--grey-text);
  }
  .step-col + .step-col { border-left: 1px solid var(--rule); }
  .num {
    width: 38px; height: 38px; border-radius: 50%;
    background: var(--black); color: var(--white);
    font-family: "Montserrat", sans-serif; font-weight: 700; font-size: 18px;
    display: flex; align-items: center; justify-content: center;
    margin: 0 auto 24px;
  }
  .step-col p { min-height: 72px; }
  .amount {
    margin-top: 18px;
    font-family: "Montserrat", sans-serif; font-weight: 800; font-size: 13px; color: var(--ink);
  }
  .web {
    margin-top: 42px;
    font-family: "Montserrat", sans-serif; font-weight: 600; font-size: 9px; color: var(--ink);
  }

  /* ---------- Guide (right) ---------- */
  .guide { background: var(--black); }
  .guide-brand { position: absolute; top: 34px; width: 100%; text-align: center; }
  .guide-brand .brand-name { font-size: 34px; color: var(--white); }
  .guide-card {
    position: absolute; left: 18px; right: 18px; top: 120px; bottom: 30px;
    background: var(--white); border-radius: 0 0 14px 14px;
  }
  .guide-wave { position: absolute; left: 0; top: 0; width: 100%; height: 40px; }
  .guide-inner { position: relative; padding: 70px 26px 0 22px; }
  .guide-title {
    text-align: center;
    font-family: "Montserrat", sans-serif; font-weight: 700;
    font-size: 14px; color: var(--orange-deep); text-transform: uppercase;
  }
  .guide-steps { list-style: none; margin-top: 26px; }
  .guide-step { display: flex; gap: 14px; align-items: center; margin-bottom: 28px; }
  .guide-step .num { margin: 0; width: 46px; height: 46px; font-size: 22px; flex-shrink: 0; }
  .guide-step h3 {
    font-family: "Montserrat", sans-serif; font-weight: 800;
    font-size: 12px; color: var(--orange-deep); margin-bottom: 4px;
  }
  .guide-step p { font-size: 9px; line-height: 1.45; color: var(--grey-text); }
  .help-note {
    font-family: "Montserrat", sans-serif; font-weight: 700;
    font-size: 10px; color: var(--ink); margin-top: -4px;
  }
  .cta {
    display: block; width: 176px; margin: 16px auto 0;
    background: var(--orange-deep); color: var(--white);
    font-family: "Montserrat", sans-serif; font-weight: 700; font-size: 14px;
    text-align: center; padding: 9px 0; border-radius: 20px; letter-spacing: .5px;
  }
</style>
</head>
<body>
<main class="pamphlet">

  <!-- Cover panel -->
  <section class="panel cover">
    <svg class="cover-top" viewBox="0 0 376 120" preserveAspectRatio="none" aria-hidden="true">
      <path d="M0 0 H376 V100 C300 70 230 118 150 98 C90 82 40 70 0 96 Z" fill="#ffffff"/>
    </svg>
    <p class="cover-kicker">ARE YOU A RECURRING DONOR YET?</p>
    <div class="cover-icon" role="img" aria-label="Small flame emblem"></div>
    <h1 class="cover-title">Are you a recurring donor <span class="accent">yet?</span></h1>
    <p class="cover-lead">Give with purpose every month<br>and help our ministry grow.</p>
    <div class="cover-brand">
      <div class="brand brand-name">VELTO</div>
      <div class="brand-tag">A CHURCH ON FIRE</div>
    </div>
    <div class="flame" style="left:-60px; bottom:-40px; width:170px; height:420px;" role="img" aria-label="Rising flames artwork"></div>
    <div class="flame" style="right:-50px; bottom:-40px; width:150px; height:260px;" role="img" aria-label="Rising flames artwork"></div>
    <p class="cover-foot">VELTO CHURCH</p>
  </section>

  <!-- Middle panel -->
  <section class="panel inside">
    <article class="inside-card invite">
      <div class="flame" style="left:-40px; top:0; width:70px; height:280px;" role="img" aria-label="Flame border artwork"></div>
      <div class="flame" style="right:-40px; top:0; width:70px; height:280px;" role="img" aria-label="Flame border artwork"></div>
      <div class="card-content">
        <span class="pill">Invitation</span>
        <h2 class="invite-title">Partner with VELTO<br>in Building the Kingdom</h2>
        <p class="body-copy">Your faithful monthly gift fuels outreach, worship<br>and care for families in our community.</p>
        <div class="benefits">
          <div class="benefit">
            <div class="benefit-icon">
              <svg width="22" height="22" viewBox="0 0 22 22" aria-hidden="true"><rect x="2" y="4" width="18" height="15" rx="2" fill="none" stroke="#e0641c" stroke-width="2"/><path d="M2 9 H20 M7 2 V6 M15 2 V6" stroke="#e0641c" stroke-width="2"/></svg>
            </div>
            Set up once<br>in minutes
          </div>
          <div class="benefit">
            <div class="benefit-icon">
              <svg width="22" height="22" viewBox="0 0 22 22" aria-hidden="true"><rect x="3" y="9" width="16" height="11" rx="2" fill="none" stroke="#e0641c" stroke-width="2"/><path d="M7 9 V6 a4 4 0 0 1 8 0 V9" fill="none" stroke="#e0641c" stroke-width="2"/></svg>
            </div>
            Secure online<br>giving
          </div>
          <div class="benefit">
            <div class="benefit-icon">
              <svg width="22" height="22" viewBox="0 0 22 22" aria-hidden="true"><circle cx="11" cy="7" r="4" fill="#e0641c"/><path d="M3 20 a8 7 0 0 1 16 0 Z" fill="#e0641c"/></svg>
            </div>
            Support people<br>in need
          </div>
        </div>
      </div>
    </article>

    <article class="inside-card steps-overview">
      <div class="flame" style="left:-40px; top:0; width:70px; height:510px;" role="img" aria-label="Flame border artwork"></div>
      <div class="flame" style="right:-40px; top:0; width:70px; height:510px;" role="img" aria-label="Flame border artwork"></div>
      <div class="card-content">
        <span class="pill">How to set up now</span>
        <p class="body-copy">Choose an amount that fits your budget<br>and give automatically each month.</p>
        <div class="step-columns">
          <div class="step-col"><div class="num">1</div><p>Pick a monthly gift that works for you</p><div class="amount">$25</div></div>
          <div class="step-col"><div class="num">2</div><p>Enter your card or bank details safely</p><div class="amount">$50</div></div>
          <div class="step-col"><div class="num">3</div><p>Confirm and start giving every month</p><div class="amount">$100</div></div>
        </div>
        <p class="web">www.veltochurch.org</p>
      </div>
    </article>
  </section>

  <!-- Right panel -->
  <section class="panel guide">
    <div class="guide-brand">
      <div class="brand brand-name">VELTO</div>
      <div class="brand-tag">A CHURCH ON FIRE</div>
    </div>
    <div class="flame" style="left:-50px; bottom:0; width:120px; height:420px;" role="img" aria-label="Rising flames artwork"></div>
    <div class="flame" style="right:-50px; bottom:0; width:120px; height:420px;" role="img" aria-label="Rising flames artwork"></div>
    <div class="guide-card">
      <svg class="guide-wave" viewBox="0 0 340 40" preserveAspectRatio="none" aria-hidden="true">
        <path d="M0 0 H340 V0 C260 40 140 0 60 30 C30 40 10 30 0 20 Z" fill="#0d0d0d"/>
      </svg>
      <div class="guide-inner">
        <h2 class="guide-title">How to set up recurring donations</h2>
        <ol class="guide-steps">
          <li class="guide-step"><div class="num">1</div><div><h3>STEP 1</h3><p>Visit our give platform and create a free donor account.</p></div></li>
          <li class="guide-step"><div class="num">2</div><div><h3>STEP 2</h3><p>Choose your amount and select the recurring monthly option.</p></div></li>
          <li class="guide-step"><div class="num">3</div><div><h3>STEP 3</h3><p>Add your payment method and pick a start date.</p></div></li>
          <li class="guide-step"><div class="num">4</div><div><h3>STEP 4</h3><p>Review your details and confirm your recurring gift.</p></div></li>
        </ol>
        <p class="help-note">Need help? See us Sunday</p>
        <span class="cta">YOU'RE ALL SET</span>
      </div>
    </div>
  </section>

</main>
</body>
</html>
```